Sophisticated, clean website reflecting my feminine, playful side to sell my abstract art,

I need a website no more than 3 pages to showcase my paintings, a little about me and some contact info. I do abstracts so looking for something a little edgy, yet feminine and current.
Updates

Hi there, These are some artists websites that I Iike: Marnelvoss.com (I like how airy it is) peterwallombry.com garethpolvens.com (I like how it scrolls) I'll need a place for a photo ( a headshot-i do not have it yet so I'll need to be able to upload that later) as well as an area for my bio. Also, it's important that I will be able to upload any new photos and descriptions easily so it should be user friendly. Lastly, I like in a sunny place so would like to have this seem upbeat and playful as that is how i like to paint. thanks-I'm trying to upload my photos now -

Target Market(s)

ppl ages 35-70 who want large scale art for their homes

Industry/Entity Type

art

Coding

Coded - Design and coding required

Number of Pages Required

3 page

Colors

Designer to choose colors to be used in the design.

Requirements
Must have
• photos of my art, a place for my bio, be easy to reach me. tasteful-nothing too "in your face" -my clients are pretty high end and organized. They like clean lines
Nice to have
• sophisticated background, muted tones in the back-similar clean font throughout-no cursive
Should not have
• too many dark areas. Too many blocks of color. Too serious.

```html
<!DOCTYPE html>
<html lang="en">
<head>
<meta charset="UTF-8">
<title>About — Lena Marlowe</title>
<link href="https://fonts.googleapis.com/css2?family=Oswald:wght@300&family=Baloo+2:wght@400;500&display=swap" rel="stylesheet">
<style>
  :root {
    --ink: #111111;
    --paper: #ffffff;
    --sun: #f2d84b;
    --rule: #8a8a8a;
    --portrait-light: #e4e8ec;
    --portrait-mid: #c9cdd2;
    --portrait-warm: #b89a86;
  }
  * { margin: 0; padding: 0; box-sizing: border-box; }
  html, body {
    width: 1200px; height: 858px; overflow: hidden;
    background: var(--paper); color: var(--ink);
    font-family: "Baloo 2", sans-serif;
  }
  .page { position: relative; width: 1200px; height: 858px; }

  .brand {
    position: absolute; top: 36px; left: 0; width: 1200px;
    text-align: center;
    font-family: "Oswald", sans-serif; font-weight: 300;
    font-size: 26px; letter-spacing: 4px; color: var(--ink);
  }
  .brand-rule {
    position: absolute; top: 109px; left: 514px; width: 172px;
    border-top: 1px solid var(--rule);
  }
  .main-nav {
    position: absolute; top: 132px; left: 0; width: 1200px;
    display: flex; justify-content: center; gap: 48px;
    font-family: "Oswald", sans-serif; font-weight: 300; font-size: 18px;
  }
  .main-nav a { color: var(--ink); text-decoration: none; }
  .main-nav a.is-current { color: var(--sun); }

  .portrait {
    position: absolute; left: 42px; top: 242px; width: 558px; height: 348px;
    border: 2px solid var(--ink);
    background:
      radial-gradient(ellipse 32% 48% at 52% 42%, var(--portrait-warm) 0%, rgba(184,154,134,0) 100%),
      linear-gradient(180deg, var(--portrait-light) 0%, var(--portrait-mid) 100%);
  }

  .bio { position: absolute; left: 625px; top: 283px; width: 410px; }
  .bio-text { font-size: 13.4px; line-height: 21px; }
  .bio-points { list-style: none; margin-top: 11px; }
  .bio-points li {
    position: relative; padding-left: 17px;
    font-size: 13.4px; font-weight: 500; line-height: 27px;
  }
  .bio-points li::before {
    content: ""; position: absolute; left: 0; top: 10px;
    width: 8px; height: 8px; border-radius: 50%; background: var(--ink);
  }

  .contact-line {
    position: absolute; left: 625px; top: 520px;
    display: flex; align-items: center; gap: 10px; font-size: 13.4px;
  }
  .social { position: absolute; left: 625px; top: 560px; display: flex; gap: 26px; }
  .social-link {
    display: block; width: 29px; height: 29px;
    border: 1.5px solid var(--ink); border-radius: 50%;
  }

  .site-footer {
    position: absolute; top: 826px; left: 0; width: 1200px;
    text-align: center; font-size: 11px;
  }
</style>
</head>
<body>
<div class="page">
  <header>
    <div class="brand">LENA MARLOWE</div>
    <div class="brand-rule"></div>
    <nav class="main-nav">
      <a href="#">GALLERY</a>
      <a href="#" class="is-current">ABOUT</a>
      <a href="#">CONTACT</a>
    </nav>
  </header>

  <div class="portrait" role="img" aria-label="Headshot of the artist smiling in a white t-shirt against a pale wall"></div>

  <section class="bio">
    <p class="bio-text">Lorem ipsum dolor sit amet, consectetuer adipiscing elit. Aenean commodo ligula eget dolor. Aenean massa. Cum sociis natoque penatibus et magnis dis parturient montes, nascetur ridiculus mus. Donec quam felis, ultricies nec, pellentesque eu, pretium quis, sem. Nulla consequat massa quis enim.</p>
    <ul class="bio-points">
      <li>Donec pede justo, fringilla vel, aliquet nec, vulputate eget, arcu.</li>
      <li>In enim justo, rhoncus ut, imperdiet a, venenatis vitae, justo.</li>
      <li>Aenean leo ligula, porttitor eu, consequat vitae, eleifend ac, enim.</li>
    </ul>
  </section>

  <div class="contact-line">
    <svg width="17" height="13" viewBox="0 0 17 13" aria-hidden="true">
      <rect x="0" y="0" width="17" height="13" rx="1.5" fill="var(--ink)"/>
      <path d="M1 1.5 L8.5 7.5 L16 1.5" fill="none" stroke="var(--paper)" stroke-width="1.4"/>
    </svg>
    <span>contact@LenaMarloweAbstract.com</span>
  </div>

  <nav class="social" aria-label="Social profiles">
    <a href="#" class="social-link" aria-label="Photo profile"></a>
    <a href="#" class="social-link" aria-label="Community page"></a>
    <a href="#" class="social-link" aria-label="News feed"></a>
  </nav>

  <footer class="site-footer">©2022 Lena Marlowe Art. All rights reserved.</footer>
</div>
</body>
</html>
```